Business card for law firm

Need business card for new law firm. Think confident, authoritative, conservative, but not stuffy or old-fashioned.

Contact Information for Business Card

Content for card - logo (uploaded), plus the following:

Paul Whitcombe (larger font)
Managing Partner (larger font, but not as large as name)
Level 9, 7 Ferris Lane
Sydney NSW 2000
Main Tel 02 9364 2710
Direct Tel 02 8472 3159
Email paul@qvlegal.com.au
www.qvlegal.com.au

Letterhead design should include logo plus:
Level 9, 7 Ferris Lane
Sydney NSW 2000
Tel 02 8472 3159
www.qvlegal.com.au

```html
<!DOCTYPE html>
<html lang="en">
<head>
<meta charset="utf-8">
<title>Quayvale Legal — Letterhead</title>
<link rel="stylesheet" href="https://fonts.googleapis.com/css2?family=Didact+Gothic&family=Tinos&display=swap">
<style>
  :root {
    --backdrop: #e4e5e7;
    --paper: #f1f1f2;
    --paper-shade: #e9e9eb;
    --navy: #0f1f57;
    --band: #0b0b0c;
    --band-text: #f4f4f4;
    --ink: #5a5a5c;
    --greeting: #4a4a4c;
    --signature-ink: #c9d3e6;
  }
  * { box-sizing: border-box; margin: 0; padding: 0; }
  html, body {
    width: 1024px; height: 1200px; overflow: hidden;
    background: var(--backdrop);
  }
  .letterhead {
    position: absolute; left: 120px; top: 50px;
    width: 784px; height: 1100px;
    background: linear-gradient(90deg, var(--paper) 0%, var(--paper) 72%, var(--paper-shade) 72%, var(--paper-shade) 100%);
    box-shadow: 0 10px 30px rgba(0,0,0,0.12);
    font-family: "Didact Gothic", "Century Gothic", sans-serif;
    color: var(--ink);
  }
  .accent-block {
    position: absolute; left: 0; top: 98px; width: 42px; height: 70px;
    background: var(--navy);
  }
  .firm-name {
    position: absolute; left: 77px; top: 96px; width: 150px;
    text-align: center;
    font-family: "Tinos", "Times New Roman", serif;
    font-size: 21px; line-height: 26px; letter-spacing: 2px;
    color: var(--navy);
  }
  .contact-band {
    position: absolute; left: 264px; top: 98px; right: 0; height: 70px;
    background: var(--band); color: var(--band-text);
    font-family: "Tinos", "Times New Roman", serif;
    font-size: 15px; line-height: 18px;
  }
  .band-address { position: absolute; left: 32px; top: 17px; }
  .band-divider {
    position: absolute; left: 241px; top: 14px; width: 1px; height: 42px;
    background: #6a6a6a;
  }
  .band-links { position: absolute; left: 316px; top: 17px; }
  .band-links div { display: flex; align-items: center; gap: 6px; }
  .band-links svg { width: 11px; height: 11px; fill: var(--band-text); }
  .greeting {
    position: absolute; left: 73px; top: 287px;
    font-size: 20px; color: var(--greeting);
  }
  .letter-body {
    position: absolute; left: 73px; top: 345px; width: 648px;
    font-size: 11.6px; line-height: 14px; text-align: justify;
  }
  .letter-body p { margin-bottom: 14px; }
  .sign-off {
    position: absolute; left: 73px; top: 696px; font-size: 11.6px;
  }
  .signature {
    position: absolute; left: 73px; top: 762px; width: 135px; height: 65px;
    background: linear-gradient(90deg, var(--signature-ink), rgba(201,211,230,0.3));
    border-radius: 4px;
  }
</style>
</head>
<body>
  <main class="letterhead">
    <div class="accent-block"></div>
    <div class="firm-name">QUAYVALE<br>LEGAL</div>

    <header class="contact-band">
      <div class="band-address">Level 9, 7 Ferris Lane<br>Sydney NSW 2000</div>
      <div class="band-divider"></div>
      <div class="band-links">
        <div>
          <svg viewBox="0 0 24 24" aria-hidden="true"><path d="M6.6 10.8a15.1 15.1 0 0 0 6.6 6.6l2.2-2.2a1 1 0 0 1 1-.25 11.4 11.4 0 0 0 3.6.57 1 1 0 0 1 1 1V20a1 1 0 0 1-1 1A17 17 0 0 1 3 4a1 1 0 0 1 1-1h3.5a1 1 0 0 1 1 1c0 1.25.2 2.45.57 3.6a1 1 0 0 1-.25 1z"/></svg>
          <span>02 8472 3159</span>
        </div>
        <div>
          <svg viewBox="0 0 24 24" aria-hidden="true"><path d="M12 2a10 10 0 1 0 0 20 10 10 0 0 0 0-20zm6.9 6h-2.9a15.6 15.6 0 0 0-1.4-3.6A8 8 0 0 1 18.9 8zM12 4a14 14 0 0 1 1.9 4h-3.8A14 14 0 0 1 12 4zM4.3 14a8 8 0 0 1 0-4h3.4a16.5 16.5 0 0 0 0 4zm.8 2h2.9a15.6 15.6 0 0 0 1.4 3.6A8 8 0 0 1 5.1 16zM8 8H5.1a8 8 0 0 1 4.3-3.6A15.6 15.6 0 0 0 8 8zm4 12a14 14 0 0 1-1.9-4h3.8A14 14 0 0 1 12 20zm2.3-6H9.7a14.7 14.7 0 0 1 0-4h4.6a14.7 14.7 0 0 1 0 4zm.3 5.6a15.6 15.6 0 0 0 1.4-3.6h2.9a8 8 0 0 1-4.3 3.6zM16.3 14a16.5 16.5 0 0 0 0-4h3.4a8 8 0 0 1 0 4z"/></svg>
          <span>www.qvlegal.com.au</span>
        </div>
      </div>
    </header>

    <p class="greeting">Dear Mr. Harlow,</p>

    <section class="letter-body">
      <p>Lorem ipsum dolor sit amet, consectetur adipiscing elit. Donec orci purus, luctus vitae dignissim eu, iaculis sed purus. Vivamus faucibus, ipsum nec aliquet viverra, leo mauris condimentum ligula, sit amet sagittis enim ligula quis arcu. Nam egestas tortor id nisi porttitor mattis. In tortor ante, ultricies in suscipit a, tempus non massa. Vivamus et auctor mi. Fusce vel massa nulla. Phasellus nec eros mauris, et scelerisque orci.</p>
      <p>Donec malesuada orci vitae nulla accumsan porta a id massa. Quisque accumsan iaculis magna sit amet fringilla. Maecenas consequat, magna eget tincidunt semper, odio nibh rutrum mi, id feugiat ante nisi eu risus. Vestibulum nunc orci, rhoncus a placerat in, ultricies in mi. Cras mattis varius eros, vel fringilla nisi suscipit eget. Quisque scelerisque sagittis nulla at porttitor.</p>
      <p>Sed id augue vitae urna euismod commodo aliquet a quam. Pellentesque arcu velit, cursus et malesuada ut, consequat et diam. Nullam erat sem, rhoncus id ullamcorper vitae, rhoncus et arcu. In ultricies ultricies nulla, ut rutrum nisi iaculis at. Donec eu magna a metus ornare faucibus. Fusce aliquet faucibus ultricies. Morbi semper, est id tincidunt gravida, sem arcu adipiscing lacus, ac bibendum nulla leo eu purus. Quisque nec diam sed risus consectetur accumsan quis quis nibh. Vestibulum id purus lorem.</p>
      <p>It is a long established fact that a reader will be distracted by the readable content of a page when looking at its layout. The point of using Lorem Ipsum is that it has a more-or-less normal distribution of letters, as opposed to using 'Content here, content here', making it look like readable English. Many desktop publishing packages</p>
    </section>

    <p class="sign-off">Sincerely,</p>
    <div class="signature" role="img" aria-label="Handwritten signature of James Harlow in blue ink"></div>
  </main>
</body>
</html>
```